Unique Business Card Design

Unique Business Card design for our orthotic and prosthetic company. Our logo is on our website, color is light blue. Unique shape (artificial leg shaped, vertical, etc..) preferred. Logo, business name, individual name and basic demographics needed.

Industry/Entity Type

Business

Contact Information for Business Card

Logo, Industry, Phone # Logo, "Prosthetic & Orthotic Services" Place to add individual name and contact info

Colors
cee9f5

Requirements
Must have
• The icon must be there, placement of "Prosthetic & Orthotic Services" can be moved
Nice to have
• Like the mix of light blue, and a little darker blue. One design included the icons from my website which was a nice touch

```html
<!DOCTYPE html>
<html lang="en">
<head>
<meta charset="utf-8">
<title>Limbwell Inc. – Business Card</title>
<link rel="stylesheet" href="https://fonts.googleapis.com/css2?family=Arimo:wght@400;700&display=swap">
<style>
  :root {
    --navy: #1f2d6b;
    --navy-dark: #16224f;
    --card: #f7f8fa;
    --card-edge: #e6e9ee;
    --text: #2e2e33;
    --page: #d9d9d6;
    --white: #ffffff;
  }
  * { margin: 0; padding: 0; box-sizing: border-box; }
  html, body {
    width: 1200px;
    height: 834px;
    overflow: hidden;
    background: var(--page);
    font-family: "Arimo", Arial, sans-serif;
  }
  .card {
    position: absolute;
    left: 150px;
    top: 162px;
    width: 900px;
    height: 510px;
    border-radius: 15px;
    background: linear-gradient(160deg, var(--white) 0%, var(--card) 60%, var(--card-edge) 100%);
    box-shadow: 0 2px 10px rgba(0,0,0,0.12);
    overflow: hidden;
  }
  .side-band {
    position: absolute;
    left: 0; top: 0;
    width: 100px;
    height: 100%;
    background: linear-gradient(180deg, var(--navy) 0%, var(--navy-dark) 100%);
  }
  .brand-dot {
    position: absolute;
    left: 28px;
    top: 31px;
    width: 136px;
    height: 136px;
    border-radius: 50%;
    background: var(--navy);
    border: 6px solid var(--white);
  }
  .brand-name {
    position: absolute;
    left: 197px;
    top: 62px;
    font-size: 34px;
    font-weight: 700;
    color: var(--navy);
    letter-spacing: 0.5px;
    line-height: 1;
  }
  .brand-rule {
    position: absolute;
    left: 197px;
    top: 104px;
    width: 321px;
    height: 2px;
    background: var(--navy);
  }
  .tagline {
    position: absolute;
    left: 214px;
    top: 112px;
    font-size: 19px;
    color: var(--navy);
    line-height: 1;
  }
  .person-name {
    position: absolute;
    left: 197px;
    top: 158px;
    font-size: 28px;
    font-weight: 700;
    color: var(--navy);
    line-height: 1;
  }
  .person-title {
    position: absolute;
    left: 197px;
    top: 198px;
    font-size: 19px;
    font-weight: 700;
    color: var(--navy);
    line-height: 1;
  }
  .contact-list {
    position: absolute;
    right: 45px;
    top: 262px;
    list-style: none;
  }
  .contact-item {
    display: flex;
    justify-content: flex-end;
    align-items: center;
    height: 34.8px;
    font-size: 21px;
    color: var(--text);
  }
  .contact-icon {
    width: 22px;
    height: 22px;
    margin-left: 14px;
    fill: var(--navy);
    flex: none;
  }
</style>
</head>
<body>
  <div class="card">
    <div class="side-band"></div>
    <div class="brand-dot"></div>

    <div class="brand-name">LIMBWELL INC.</div>
    <div class="brand-rule"></div>
    <div class="tagline">Prosthetic &amp; Orthotic Services</div>

    <div class="person-name">Miriam Talbot</div>
    <div class="person-title">CO LPO</div>

    <ul class="contact-list">
      <li class="contact-item">555.014.2200
        <svg class="contact-icon" viewBox="0 0 24 24" aria-hidden="true"><path d="M2 8c0-3 4-5 10-5s10 2 10 5v2h-5V8c-1-1-3-1.5-5-1.5S8 7 7 8v2H2z"/><path d="M6 11h12l3 9H3z"/><circle cx="12" cy="15.5" r="2.5" fill="#f7f8fa"/></svg>
      </li>
      <li class="contact-item">555.014.2291
        <svg class="contact-icon" viewBox="0 0 24 24" aria-hidden="true"><path d="M7 1h10a2 2 0 0 1 2 2v18a2 2 0 0 1-2 2H7a2 2 0 0 1-2-2V3a2 2 0 0 1 2-2zm0 3v14h10V4z"/><circle cx="12" cy="20.5" r="1.2" fill="#f7f8fa"/></svg>
      </li>
      <li class="contact-item">555-0148630
        <svg class="contact-icon" viewBox="0 0 24 24" aria-hidden="true"><path d="M6 2h9l3 3v4H6z"/><path d="M2 10h20v9H2z"/><rect x="5" y="14" width="14" height="2" fill="#f7f8fa"/><path d="M5 20h14v2H5z"/></svg>
      </li>
      <li class="contact-item">Mtalbot@limbwellinc.com
        <svg class="contact-icon" viewBox="0 0 24 24" aria-hidden="true"><path d="M2 5h20v3l-10 6L2 8z"/><path d="M2 10l10 6 10-6v9H2z"/></svg>
      </li>
      <li class="contact-item">www.limbwellinc.com
        <svg class="contact-icon" viewBox="0 0 24 24" aria-hidden="true"><circle cx="12" cy="12" r="10"/><path d="M8 6c2 1 3 3 2 5s-3 1-3 3 2 3 1 5M15 4c-1 2 1 3 3 3M17 13c-2 0-3 2-2 4s2 2 3 1" stroke="#f7f8fa" stroke-width="1.6" fill="none"/></svg>
      </li>
      <li class="contact-item">2280 W. 14th St., Fairview, NY 10990
        <svg class="contact-icon" viewBox="0 0 24 24" aria-hidden="true"><path d="M12 1a8 8 0 0 1 8 8c0 6-8 14-8 14S4 15 4 9a8 8 0 0 1 8-8z"/><circle cx="12" cy="9" r="3" fill="#f7f8fa"/></svg>
      </li>
    </ul>
  </div>
</body>
</html>
```